Computer business require Thank you flyer to include in shipments

We ship computers (mainly laptops, tablets) to customers, most shipments are single unit in a box, we like to include in each box one page flyer as a Thank you note, and also mention in the note that for any reason if the buyer is not satisfied with the purchase or they wish to return the item they can contact us and will take care of any issue.
am thinking to have the design reflect a modern look, also with some color possibly to attract the customer attention and make them read the note, as some people tend to not read paper included in shipments. I will include the content that we like to be on the flyer, however we are open to suggestions either to add more text or how to layout the contents on the page. We also have a company logo that we would like to have it on the flyer.

Target Market(s)

End user, business buyers, wholesalers

Industry/Entity Type

Business

Font styles to use
Sans Serif
Other font styles liked:
• maybe even arial or times roman, a font that would be commonly used for a flyer easy readable

Colors
3377b5
f04a50
e667a6
b868aa
33a6d7
0792cd
ec1f27

Requirements
Must have
• Company logo
Nice to have
• Possible the address somewhere on the bottom of the page either left or right or one line at the end, depending how would look with the layout.
• Not too sure about color, most likely blue similar to our logo colors would be first choice, I was also thinking just to catch buyers attention when they open the package should we do it maybe red or even pink which would be softer tone possibly making it interesting for buyer to read. I know some colors would bring more attention to say "READ ME". Or maybe I'll have 2 flyers in different colors and sent to buyers accordingly based on the gender.
Should not have
• Somehow I did not realize we had added the note section on the content, I like to remove that part that mention about "Read Below Notes...." then the two paragraph that follow about technical guide. I just want this flyer be a Thank you note as well as inform buyers to contact us directly if they have issue.

```html
<!DOCTYPE html>
<html lang="en">
<head>
<meta charset="utf-8">
<title>Thank You – Novatech International</title>
<link rel="stylesheet" href="https://fonts.googleapis.com/css2?family=Open+Sans:wght@400;600;700&display=swap">
<style>
  :root {
    --brand-blue: #0792cd;
    --deep-blue: #3377b5;
    --sky-blue: #33a6d7;
    --ink: #23445f;
    --paper: #ffffff;
    --photo-light: #f1efec;
    --photo-mid: #d9d1c6;
    --photo-warm: #b9a48c;
  }
  * { box-sizing: border-box; margin: 0; padding: 0; }
  html, body { width: 849px; height: 1200px; overflow: hidden; background: var(--paper); }
  body { font-family: "Open Sans", Arial, sans-serif; color: var(--ink); }
  .flyer { position: relative; width: 849px; height: 1200px; background: var(--paper); overflow: hidden; }

  .hero-photo {
    position: absolute; top: 0; left: 0; width: 849px; height: 470px;
    background:
      radial-gradient(ellipse 260px 200px at 560px 250px, #a9b8c6 0%, rgba(169,184,198,0) 100%),
      radial-gradient(ellipse 220px 180px at 300px 230px, #d8c2a8 0%, rgba(216,194,168,0) 100%),
      linear-gradient(160deg, var(--photo-light) 0%, var(--photo-mid) 50%, var(--photo-warm) 100%);
  }
  .brand {
    position: absolute; top: 22px; left: 30px;
    display: flex; flex-direction: column; gap: 2px;
  }
  .brand-row { display: flex; align-items: center; gap: 8px; }
  .brand-mark { width: 20px; height: 20px; background: var(--brand-blue); }
  .brand-name { font-size: 24px; font-weight: 700; color: var(--deep-blue); letter-spacing: 1px; }
  .brand-tag { font-size: 11px; font-weight: 600; color: var(--deep-blue); padding-left: 28px; }

  .hero-band { position: absolute; top: 360px; left: 0; width: 849px; height: 120px; }
  .hero-title {
    position: absolute; top: 398px; left: 14px;
    font-size: 38px; font-weight: 400; color: var(--paper); letter-spacing: 1px;
  }

  .letter {
    position: absolute; top: 500px; left: 40px; width: 770px;
    font-size: 15px; line-height: 1.62;
  }
  .letter p { margin-bottom: 17px; }
  .letter strong { font-weight: 700; color: var(--deep-blue); }

  .footer-rule {
    position: absolute; top: 1128px; left: 24px; width: 801px; height: 3px;
    background: var(--brand-blue);
  }
  .contact {
    position: absolute; top: 1144px; left: 0; width: 849px; text-align: center;
    color: var(--deep-blue); font-size: 13px; font-weight: 700; line-height: 1.55;
  }
  .contact .sep { padding: 0 10px; font-weight: 400; }
</style>
</head>
<body>
<div class="flyer">
  <div class="hero-photo" role="img" aria-label="Photo of a smiling family relaxing on a sofa around a laptop computer"></div>

  <div class="brand">
    <div class="brand-row">
      <span class="brand-mark"></span>
      <span class="brand-name">NOVATECH INTERNATIONAL</span>
    </div>
    <span class="brand-tag">Computer &amp; Electronics Wholesaler</span>
  </div>

  <svg class="hero-band" viewBox="0 0 849 120" preserveAspectRatio="none" aria-hidden="true">
    <defs>
      <linearGradient id="bandFill" x1="0" y1="0" x2="1" y2="0">
        <stop offset="0" stop-color="#0792cd"/>
        <stop offset="0.55" stop-color="#33a6d7" stop-opacity="0.75"/>
        <stop offset="1" stop-color="#33a6d7" stop-opacity="0"/>
      </linearGradient>
    </defs>
    <path d="M0 20 C 200 0, 420 40, 849 30 L 849 110 L 0 110 Z" fill="url(#bandFill)"/>
    <path d="M0 105 C 300 95, 560 118, 849 108 L 849 120 L 0 120 Z" fill="#ffffff"/>
  </svg>
  <div class="hero-title">THANK YOU</div>

  <div class="letter">
    <p>Dear Customer,</p>
    <p>Thank you for your purchase.</p>
    <p>We very much appreciate your business, it has been a pleasure serving you.<br>
    <strong>Customer satisfaction is our #1 priority</strong>, at the same time our commitment is to provide quality products with exceptional customer service.</p>
    <p>We hope you have received your item in good condition and in a timely manner.</p>
    <p>Please keep the original packaging just in case you would require to return the item. We respectfully ask if you are in any way unhappy with your purchase, either having remorse, change of mind or an issue with the item received even during warranty period, please contact us directly via email at customerservice@novatech-intl.com or call us Toll Free at (888) 555-0142 during business hours Monday - Friday, 9am to 4pm PST and give us the opportunity to make it right for you, we are committed to ensuring that you are completely satisfied with your purchase, appreciate your patience until we solve any issue, we value your business and would like to address your concern as quickly as possible.</p>
    <p>If you have been satisfied with our product and service we would greatly appreciate a moment of your time to leave your positive feedback for this transaction on the website of purchase, your opinion would allow us to maintain our high standards in providing a wonderful buying experience for all customers.</p>
  </div>

  <div class="footer-rule"></div>
  <div class="contact">
    <div>sales@novatech-intl.com<span class="sep">|</span>www.novatech-intl.com<span class="sep">|</span>Toll Free : 1-888-555-0142</div>
    <div>2740 W. Harbor Ave., Fairview, CA 90210</div>
  </div>
</div>
</body>
</html>
```